Gaming company needs web presence

PLEASE NOTE: We need just a simple web site. We are at least a year away from launching our first product, so the site only needs a small amount of information on it. The only people who will be visiting the web site are prospective employees, prospective investors who want a little information on the company, journalists who want a little more information, and people in the games industry who will visit to read blog posts about the development of our first game.

Lanternfield Games is a new gaming company that wants to change how people think about video games. We are making games that we think can be so interesting to watch that people might want to tune into them instead of the TV.

The games we make are sophisticated, they are not for children, and we want to project an image of being serious about our craft and the brand we're trying to create. Our games are heavily focused on players interacting with each other in sophisticated ways: to negotiate, to compete, to fight, to come to each other's rescue, to cheer each other on, or to simply watch each other in awe.

We do not want a site that features lots of video game cliches like joysticks, 8 bit graphics, science fiction themes, or military themes. We are focused on craftsmanship, so we'd like to project a sense of precision, pride and deep purpose.

The purpose of this website is to create an image of our company that can help us recruit like-minded craftspeople and help find business partners. There will be no e-commerce, account creation, or forums for some time. The site should have:
-A front page that describes our business
-A section that describes our first game (we have only one for now)
-A section for employees to write blog posts. There should be something on the home page that shows links to the latest 3 blog posts.
-A section about founders that shows information about them.
-Contact information, lets people send us email

Our first game is one that looks very realistic. It takes place on a tropical island. We can't say a lot more about it in public yet, but I will say these things: it is not a game that children will play, it is not very violent, it would look more like a film than a typical video game.

And the site should be easily extendable when we have more content and more categories of content.

I've attached our official company logo with a color scheme we've been using, plus an alternate version of the logo. Please use this as a starting point for the web site's visual design. Also, I do not think it is necessary to use the dark background in the logo as the background throughout the site. I wouldn't rule it out, but I'd like to see some proposals with lighter backgrounds.

We need to be able to get code from you so that we can drop it on our server and get it running without extra effort. We need to be able to add content for Blog posts easily as well, so please indicate how that would work.
Updates

Hello everyone, Thanks for all of the great submissions so far. There are some important things I'd like to relay to everyone: We are at least a year away from launching our first game, so we only need a simple web site. Unfortunately, we can't share any screenshots or details about our first game yet. All of these submissions look great, but are far too complicated. Also, I really want to stress that we don't want to feature stock photography of people playing games, especially of children playing games. In fact, since we don't want to release any screenshots of our games and we don't have any good photography of ourselves working, it's best if there are no photographic images on the site for now.

Hello designers, Can you let me know if your designs include all the code that would let us drop the files on to our web server and easily get it up and running? Also, can you tell me how the blog posts would be created? Does your code run on a CMS? Thanks, Haskell

Hi Designers, we will be hosting this site with Wordpress, so we would prefer to have submissions ready to go on a Wordpress server. Thanks!

Target Market(s)

Investors, prospective employees, press, blog post readers.

Industry/Entity Type

Business

Font styles to use
Sans Serif

Requirements
Must have
• Simplicity first. Please use a color palette and fonts that match our logo.
Should not have
• Video game cliches. Flash animations or menus.
No children.
No photographs of people playing games.

(I realize this is very limiting, but we're keeping the sits as simple as possible for now)

```html
<!DOCTYPE html>
<html lang="en">
<head>
<meta charset="utf-8">
<title>Lanternfield Games</title>
<link rel="stylesheet" href="https://fonts.googleapis.com/css2?family=Oswald:wght@400;500;700&family=Arimo:wght@400;700&display=swap">
<style>
:root{
  --bg:#4a2208;
  --bg-deep:#3d1c06;
  --orange:#e0801c;
  --cream:#f4e6d4;
  --muted:#9a6a44;
  --link:#d58a4a;
  --btn:#3a1a05;
  --nav-ink:#5a1404;
  --white:#ffffff;
}
*{margin:0;padding:0;box-sizing:border-box}
html,body{width:1083px;height:1200px;overflow:hidden;background:var(--bg)}
body{position:relative;font-family:"Arimo",Arial,sans-serif;color:var(--cream)}
.abs{position:absolute}
.hero-art{left:0;top:0;width:1083px;height:590px;
  background:radial-gradient(ellipse 420px 300px at 470px 300px,#e8d0b2 0%,#b88458 45%,rgba(74,34,8,0) 100%),
  linear-gradient(180deg,#6a3a1a 0%,#8a5a34 40%,#7a4826 70%,var(--bg) 100%)}
.brand{left:163px;top:22px;display:flex;align-items:center;gap:14px}
.brand-name{font-family:"Oswald",sans-serif;font-weight:700;font-size:44px;color:var(--white);letter-spacing:3px;line-height:1}
.brand-dot{width:40px;height:40px;border-radius:50%;background:var(--orange)}
.social{display:flex;gap:8px}
.social span{width:19px;height:19px;border-radius:50%;display:block}
.s1{background:#29b6e8}.s2{background:#3b5a9a}.s3{background:#c9402c}.s4{background:#e4508a}.s5{background:#d21e1e}
.social-top{left:780px;top:113px}
.nav{left:163px;top:150px;width:758px;height:46px;
  background:linear-gradient(180deg,#f39a1c 0%,#e06c10 55%,#b8220c 88%,#f08a1a 88%,#f08a1a 100%);
  display:flex;align-items:center;padding:0 24px 5px;gap:58px}
.nav a{font-family:"Oswald",sans-serif;font-weight:500;font-size:12px;color:var(--nav-ink);text-decoration:none;text-transform:uppercase}
.nav a.active{color:var(--white)}
.hero-title{left:163px;top:296px;font-family:"Oswald",sans-serif;font-weight:700;font-size:46px;color:var(--white);letter-spacing:-1px;line-height:1;text-shadow:2px 2px 3px rgba(0,0,0,.5)}
.hero-title em{font-style:normal;color:var(--orange)}
.hero-text{left:163px;top:356px;width:340px;font-size:12.5px;line-height:16px;color:var(--white)}
.btn{background:var(--btn);color:var(--white);font-family:"Oswald",sans-serif;font-weight:500;text-transform:uppercase;text-decoration:none;display:flex;align-items:center;justify-content:center;border-radius:3px;box-shadow:0 3px 0 #2a1002}
.btn-play{left:163px;top:422px;width:114px;height:45px;font-size:15px}
.dots{left:512px;top:534px;display:flex;gap:13px}
.dots span{width:10px;height:10px;border-radius:50%;border:1.5px solid var(--white)}
.dots .on{background:var(--white)}
.welcome-title{left:0;width:1083px;top:602px;text-align:center;font-family:"Oswald",sans-serif;font-weight:500;font-size:21px;color:var(--orange);letter-spacing:-.5px}
.welcome-text{left:200px;width:683px;top:648px;text-align:center;font-size:12.5px;line-height:16px;color:var(--cream)}
.btn-more{left:499px;top:714px;width:85px;height:36px;font-size:11.5px}
.divider{left:170px;top:784px;width:740px;height:2px;background:radial-gradient(ellipse at center,rgba(20,6,0,.6),rgba(20,6,0,0) 70%)}
.glow{left:300px;top:786px;width:480px;height:320px;background:radial-gradient(ellipse at 50% 0,rgba(120,60,20,.5),rgba(74,34,8,0) 70%)}
.section-title{font-family:"Oswald",sans-serif;font-weight:500;font-size:15px;color:var(--orange);text-transform:uppercase;letter-spacing:-.3px}
.blog-title{left:177px;top:823px}
.blog-feature{left:177px;top:865px;width:250px;height:147px;background:radial-gradient(ellipse at 50% 45%,#8ab048 0%,#3d6a26 60%,#24401a 100%)}
.thumbs{left:177px;top:1016px;display:flex;gap:3px}
.thumbs div{width:60px;height:49px;border:2px solid #7a3a14}
.t1{background:linear-gradient(135deg,#5a8a30,#2e5418)}
.t2{background:linear-gradient(135deg,#8a7a68,#4a3a2a)}
.t3{background:linear-gradient(180deg,#7ab4e0,#b04a2a)}
.t4{background:linear-gradient(135deg,#b8d060,#6a9a30)}
.posts{left:452px;top:862px;width:190px;list-style:none}
.post{margin-bottom:13px}
.post h3{font-size:13px;font-weight:700;color:var(--white);line-height:16px}
.post .meta{font-size:9.5px;color:var(--link);margin-top:4px}
.post .excerpt{font-size:9.8px;line-height:14px;color:var(--muted);margin-top:5px}
.founders-title{left:675px;top:823px}
.arrows{left:866px;top:826px;display:flex;gap:14px}
.founder{left:675px;display:flex;gap:14px}
.avatar{width:58px;height:58px;border-radius:50%;border:2px solid #7a3a14;background:radial-gradient(circle at 50% 40%,#b07a4e,#3a1e0e)}
.founder h3{font-size:13px;font-weight:400;color:var(--white);margin-top:12px}
.founder p{font-size:9.8px;line-height:12.5px;color:var(--orange);margin-top:6px;width:165px}
.footer{left:0;top:1118px;width:1083px;height:82px;background:var(--bg-deep);border-top:1px solid #5e3014}
.footer-nav{left:179px;top:1141px;display:flex;gap:11px;font-size:10.5px;color:var(--muted)}
.copyright{left:179px;top:1164px;font-size:10.5px;color:var(--muted)}
.social-bottom{left:780px;top:1150px}
</style>
</head>
<body>
<div class="abs hero-art" role="img" aria-label="Warm sepia island landscape in morning mist"></div>

<header>
  <div class="abs brand"><span class="brand-name">LANTERNFIELD GAMES</span><span class="brand-dot"></span></div>
  <div class="abs social social-top"><span class="s1"></span><span class="s2"></span><span class="s3"></span><span class="s4"></span><span class="s5"></span></div>
  <nav class="abs nav">
    <a class="active" href="#">Home</a>
    <a href="#">Our Game</a>
    <a href="#">Blog</a>
    <a href="#">Founders</a>
    <a href="#">Careers</a>
    <a href="#">Contact</a>
  </nav>
</header>

<section class="hero">
  <h1 class="abs hero-title">GAMES WORTH <em>WATCHING</em></h1>
  <p class="abs hero-text">We craft games where players negotiate, compete and rescue each other, stories so rich you may tune in instead of the TV.</p>
  <a class="abs btn btn-play" href="#">Our Game</a>
  <div class="abs dots"><span></span><span class="on"></span><span></span></div>
</section>

<section class="welcome">
  <h2 class="abs welcome-title">WELCOME TO LANTERNFIELD GAMES</h2>
  <p class="abs welcome-text">We are a new studio built on craftsmanship, precision and deep purpose. Our first game, set on a tropical island, is made for adults and plays more like a film than a typical video game.</p>
  <a class="abs btn btn-more" href="#">Read More</a>
</section>

<div class="abs divider"></div>
<div class="abs glow"></div>

<section class="blog">
  <h2 class="abs section-title blog-title">Latest Blog Posts</h2>
  <div class="abs blog-feature" role="img" aria-label="Soft green island concept art for the latest post"></div>
  <div class="abs thumbs">
    <div class="t1" role="img" aria-label="Post image, jungle clearing"></div>
    <div class="t2" role="img" aria-label="Post image, stone ruins"></div>
    <div class="t3" role="img" aria-label="Post image, sunset coast"></div>
    <div class="t4" role="img" aria-label="Post image, island village"></div>
  </div>
  <ul class="abs posts">
    <li class="post">
      <h3>Building an Island by Hand</h3>
      <p class="meta">4 January 2014 , by admin</p>
      <p class="excerpt">How our art team shapes every cliff, reef and path to feel real and lived in.</p>
    </li>
    <li class="post">
      <h3>Why Spectators Matter</h3>
      <p class="meta">28 December 2013 , by admin</p>
      <p class="excerpt">Designing play that is as gripping to watch as it is to take part in.</p>
    </li>
    <li class="post">
      <h3>Notes on Player Trust</h3>
      <p class="meta">15 December 2013 , by admin</p>
      <p class="excerpt">Negotiation, rescue and rivalry: the systems behind real cooperation.</p>
    </li>
  </ul>
</section>

<section class="founders">
  <h2 class="abs section-title founders-title">Our Founders</h2>
  <div class="abs arrows">
    <svg width="12" height="14" viewBox="0 0 12 14"><path d="M8 2 3 7l5 5" fill="none" stroke="#e0801c" stroke-width="1.6"/></svg>
    <svg width="12" height="14" viewBox="0 0 12 14"><path d="M4 2l5 5-5 5" fill="none" stroke="#e0801c" stroke-width="1.6"/></svg>
  </div>
  <div class="abs founder" style="top:862px"><div class="avatar" role="img" aria-label="Portrait of Miles Corwen"></div><div><h3>Miles Corwen</h3><p>Game director focused on player behaviour and shared stories.</p></div></div>
  <div class="abs founder" style="top:937px"><div class="avatar" role="img" aria-label="Portrait of Tobias Renner"></div><div><h3>Tobias Renner</h3><p>Art director crafting worlds that look like film.</p></div></div>
  <div class="abs founder" style="top:1012px"><div class="avatar" role="img" aria-label="Portrait of Jonah Pellham"></div><div><h3>Jonah Pellham</h3><p>Technical lead building tools for precise, lasting play.</p></div></div>
</section>

<footer class="abs footer"></footer>
<nav class="abs footer-nav"><span>Home</span><span>Our Game</span><span>Blog</span><span>Founders</span><span>Careers</span><span>Contact</span></nav>
<p class="abs copyright">© 2014 Lanternfield Games. All right reserved.</p>
<div class="abs social social-bottom"><span class="s1"></span><span class="s2"></span><span class="s3"></span><span class="s4"></span><span class="s5"></span></div>
</body>
</html>
```